K7 Electrical Services Ltd Web design

I require a web site for my new electrical contracting company. We are customer service orientated. Offering high value electrical installations, design and maintenance. Focused on custom residential and commercial upgrading. Lighting design and application are paramount in our company's services. Industry leading product use and integration are always on the forefront with our customer client services. As well as energy efficiency.

Target Market(s)

Homebuilders, General Contractors, Property management companies, clients, individuals,

Industry/Entity Type

Electric Company

Coding

Coded - Design and coding required

Number of Pages Required

3 page

Requirements
Must have
• Classic, modern, edgy but not trendy . Appeals to the masse.
• 3 page
• home page
• about page
• gallery page
• ability to contact from the webiste
Nice to have
• open to all types of designs that are relative to the construction industry.
• Black, Grey, metallic ice blue and deep purple colours from the logo.
Should not have
• anything cheesy with cartoon light bulb images.

```html
<!DOCTYPE html>
<html lang="en">
<head>
<meta charset="utf-8">
<title>K7 Electrical Services Ltd</title>
<link rel="stylesheet" href="https://fonts.googleapis.com/css2?family=Exo+2:wght@500;600;700&family=Open+Sans:wght@400;600;700&display=swap">
<style>
:root{
  --purple:#5c2a8c;
  --purple-dark:#4a1f73;
  --ink:#222;
  --text:#555;
  --muted:#888;
  --grey-bg:#efefef;
  --topbar:#e8e8e8;
  --cta-bg:#3a3a3a;
  --black:#1c1c1c;
  --yellow:#f3c316;
  --white:#fff;
}
*{box-sizing:border-box;margin:0;padding:0}
html,body{width:1200px;height:4412px;overflow:hidden}
body{font-family:"Open Sans",Arial,sans-serif;color:var(--text);background:var(--white);position:relative}
.abs{position:absolute}
h2,h3,h4{font-family:"Exo 2",Arial,sans-serif;color:var(--ink)}

/* top bar */
.topbar{top:0;left:0;width:1200px;height:30px;background:var(--topbar);font-size:12px;color:var(--purple)}
.topbar .item{top:8px;display:flex;align-items:center;gap:6px}
.topbar .socials{right:30px;top:7px;display:flex;gap:6px}
.diamond{width:14px;height:14px;background:var(--purple);transform:rotate(45deg)}

/* header */
.header{top:30px;left:0;width:1200px;height:110px;background:var(--white)}
.brand{left:47px;top:32px;display:flex;align-items:center;gap:10px;font-family:"Exo 2",sans-serif;font-weight:700;font-size:21px;color:var(--purple)}
.brand .mark{width:16px;height:16px;background:var(--purple)}
.contact-block{top:38px;display:flex;gap:12px;align-items:center}
.contact-block .lbl{font-size:10px;color:var(--muted);text-transform:uppercase;letter-spacing:.5px}
.contact-block .val{font-size:14px;font-weight:700;color:var(--ink)}

/* hero */
.hero{top:140px;left:0;width:1200px;height:560px;background:linear-gradient(180deg,#9fb3c6 0%,#c9d2da 35%,#7d7f82 70%,#4e4d4a 100%)}
.nav{top:150px;left:60px;width:1070px;height:46px;background:rgba(40,40,40,.88);display:flex;align-items:center}
.nav a{color:var(--white);text-decoration:none;font-size:13px;font-weight:700;padding:0 24px;height:46px;display:flex;align-items:center;text-transform:uppercase}
.nav a.active{background:var(--purple)}
.nav .quote{position:absolute;right:0;top:0;background:#1e1e1e;padding:0 28px}
.hero-title{top:338px;left:47px;width:430px;height:90px;background:rgba(30,30,30,.7);padding:10px 12px}
.hero-title h1{font-family:"Exo 2",sans-serif;font-weight:700;font-size:33px;line-height:36px;color:var(--white);text-transform:uppercase}

/* section heading */
.sec-head{left:0;width:1200px;text-align:center}
.sec-head h2{font-size:32px;font-weight:700;letter-spacing:1px;text-transform:uppercase}
.sec-head .sub{display:flex;justify-content:center;align-items:center;gap:10px;font-size:12px;color:var(--ink);margin-top:4px}
.sec-head .sub::before,.sec-head .sub::after{content:"";width:90px;height:1px;background:#aaa}

/* services */
.intro{top:828px;left:180px;width:840px;text-align:center;font-size:18px;line-height:28px;color:var(--muted)}
.service{width:300px;text-align:center}
.service svg{display:block;margin:0 auto 14px}
.service h3{font-family:"Open Sans",sans-serif;font-size:19px;font-weight:400;color:var(--ink);margin-bottom:4px}
.service p{font-size:13px;line-height:17px;color:var(--text)}

/* call to action */
.cta-band{top:1382px;left:0;width:1200px;height:156px;background:var(--cta-bg)}
.cta-photo{top:1382px;left:0;width:300px;height:156px;background:linear-gradient(120deg,#7b6a52,#b6a68b 50%,#5f5749)}
.cta-title{top:1405px;left:437px;font-size:26px;color:var(--white);font-weight:600}
.cta-text{top:1445px;left:437px;width:480px;font-size:18px;line-height:26px;color:#ddd}
.cta-btn{top:1432px;left:984px;width:168px;height:52px;border:1px solid #ccc;color:var(--white);font-size:15px;font-weight:600;display:flex;align-items:center;justify-content:center;text-transform:uppercase}

/* what we do */
.about-photo{top:1680px;left:62px;width:330px;height:350px;background:linear-gradient(150deg,#c8cdd2,#8e9aa6 55%,#3f4a5e)}
.about-text{top:1710px;left:414px;width:440px}
.about-text h3{font-size:22px;color:var(--purple-dark);font-weight:700;margin-bottom:14px}
.about-text p{font-size:13.5px;line-height:19px;margin-bottom:16px}
.form{top:1680px;left:872px;width:264px;height:350px;background:var(--purple);padding:14px 22px}
.form h3{font-size:21px;color:var(--white);font-weight:700;margin-bottom:12px;text-transform:uppercase}
.field{background:var(--white);height:38px;margin-bottom:10px;font-size:12px;color:var(--purple);padding:10px 8px}
.field.msg{height:76px}
.submit{position:absolute;right:22px;bottom:24px;background:var(--yellow);color:var(--ink);font-size:12px;font-weight:700;padding:8px 14px;text-transform:uppercase}

/* works */
.works{top:2102px;left:0;width:1200px;height:794px;background:var(--grey-bg)}
.filters{top:2256px;left:0;width:1200px;display:flex;justify-content:center;gap:22px}
.filters span{height:38px;padding:0 24px;border:1px solid #bbb;background:var(--white);font-size:14px;color:var(--ink);display:flex;align-items:center;text-transform:uppercase}
.filters span.active{background:var(--purple);border-color:var(--purple);color:var(--white)}
.grid{top:2323px;left:47px;width:1086px;height:494px;display:grid;grid-template-columns:repeat(4,1fr);grid-template-rows:repeat(2,1fr)}
.tile{width:100%;height:100%}

/* testimonials */
.quote-box{font-size:14px;line-height:21px;color:var(--white);padding:18px 22px}
.quote-box::after{content:"";position:absolute;bottom:-14px;left:130px;border:14px solid transparent;border-bottom:0;border-top-color:inherit}
.q1{top:3072px;left:75px;width:520px;height:178px;background:var(--purple);border-top-color:var(--purple)}
.q2{top:3080px;left:600px;width:525px;height:90px;background:#1f1f24;border-top-color:#1f1f24;text-align:center;padding-top:32px}
.q2::after{left:360px}
.avatar{width:94px;height:94px;border-radius:50%;border:4px solid var(--white);box-shadow:0 0 0 1px #ddd}
.person h4{font-family:"Open Sans",sans-serif;font-size:16px;color:var(--ink);font-weight:600}
.person p{font-size:13px;color:var(--text)}

/* map */
.map{top:3463px;left:0;width:1200px;height:380px;background:linear-gradient(135deg,#e9e4d6,#dfe6d2 45%,#e6e2d4)}

/* footer */
.footer{top:3843px;left:0;width:1200px;height:273px;background:var(--purple)}
.office{top:3898px;width:300px;color:var(--white)}
.office h3{color:var(--white);font-family:"Open Sans",sans-serif;font-size:25px;font-weight:400;margin-bottom:16px}
.office .row{display:flex;gap:14px;font-size:13px;line-height:18px;margin-bottom:12px}
.divider{top:3900px;width:1px;height:170px;background:rgba(255,255,255,.35)}
.bottom{top:4116px;left:0;width:1200px;height:296px;background:var(--black);text-align:center;color:var(--white)}
.bottom .brand{position:static;justify-content:center;color:#bbb;margin-top:64px}
.bottom .links{margin-top:62px;font-size:13px;text-transform:uppercase}
.bottom .copy{margin-top:6px;font-size:13px}
.bottom .socials{display:flex;justify-content:center;gap:10px;margin-top:34px}
.bottom .socials span{width:26px;height:26px;border-radius:50%;background:#ddd}
</style>
</head>
<body>

<div class="abs topbar">
  <div class="abs item" style="left:47px">
    <svg width="10" height="12" viewBox="0 0 10 12"><path d="M5 0a4 4 0 0 1 4 4c0 3-4 8-4 8S1 7 1 4a4 4 0 0 1 4-4z" fill="#5c2a8c"/></svg>14, Foundry Street, Westbrook</div>
  <div class="abs item" style="left:300px">
    <svg width="12" height="9" viewBox="0 0 12 9"><rect width="12" height="9" fill="#5c2a8c"/><path d="M0 0l6 5 6-5" stroke="#fff" fill="none"/></svg>info@k7electrical.com</div>
  <div class="abs item" style="left:495px">
    <svg width="10" height="10" viewBox="0 0 10 10"><path d="M2 0l2 3-1 1c1 2 2 3 3 3l1-1 3 2-2 2C4 10 0 6 0 2z" fill="#5c2a8c"/></svg>+1 (800) 555 - 0142</div>
  <div class="abs socials"><span class="diamond"></span><span class="diamond"></span><span class="diamond"></span><span class="diamond"></span></div>
</div>

<header class="abs header">
  <div class="abs brand"><span class="mark"></span>K7 Electrical Services Ltd</div>
  <div class="abs contact-block" style="left:530px">
    <svg width="22" height="28" viewBox="0 0 22 28"><path d="M11 1a9 9 0 0 1 9 9c0 7-9 17-9 17S2 17 2 10a9 9 0 0 1 9-9z" fill="none" stroke="#888" stroke-width="2"/><circle cx="11" cy="10" r="3" fill="#888"/></svg>
    <div><div class="lbl">Find us</div><div class="val">41, HARBOUR LANE</div></div>
  </div>
  <div class="abs contact-block" style="left:720px">
    <svg width="26" height="26" viewBox="0 0 26 26"><rect x="2" y="2" width="22" height="22" rx="3" fill="none" stroke="#888" stroke-width="2"/><path d="M8 7l3 4-2 2c1 2 2 3 4 4l2-2 4 3-2 3C11 21 5 15 5 9z" fill="#888"/></svg>
    <div><div class="lbl">Call us today</div><div class="val">+000-5550-188</div></div>
  </div>
  <div class="abs contact-block" style="left:905px">
    <svg width="28" height="22" viewBox="0 0 28 22"><rect x="1" y="1" width="26" height="20" fill="none" stroke="#888" stroke-width="2"/><path d="M1 1l13 11L27 1" fill="none" stroke="#888" stroke-width="2"/></svg>
    <div><div class="lbl">Email us now</div><div class="val">HELLO@K7ELECTRICAL.COM</div></div>
  </div>
</header>

<div class="abs hero" role="img" aria-label="Photo of a large suburban house at dusk with an electrician in blue overalls holding a coil of cable"></div>
<nav class="abs nav">
  <a class="active">Home</a><a>About</a><a>Services</a><a>Projects</a><a>Blog</a><a>Contact</a>
  <a class="quote">Request a quote</a>
</nav>
<div class="abs hero-title"><h1>Residential Electrical<br>Services</h1></div>

<div class="abs sec-head" style="top:740px"><h2>Our Services</h2><div class="sub">what we offer</div></div>
<p class="abs intro">Never hesitate when it comes to potential electrical problems. Electrical issues can quickly develop into major catastrophes.</p>

<div class="abs service" style="top:935px;left:60px">
  <svg width="50" height="62" viewBox="0 0 50 62"><path d="M12 2h26l8 28H4z" fill="#5c2a8c"/><rect x="23" y="30" width="4" height="22" fill="#5c2a8c"/><rect x="12" y="52" width="26" height="6" fill="#5c2a8c"/></svg>
  <h3>Electrical</h3><p>Wiring, Remodels &amp; Additions,<br>Heat detectors</p>
</div>
<div class="abs service" style="top:935px;left:426px">
  <svg width="60" height="62" viewBox="0 0 60 62"><g fill="#5c2a8c"><rect x="6" y="12" width="6" height="46" rx="3"/><rect x="16" y="12" width="6" height="46" rx="3"/><rect x="26" y="12" width="6" height="46" rx="3"/><rect x="36" y="12" width="6" height="46" rx="3"/><rect x="46" y="12" width="6" height="46" rx="3"/><rect x="2" y="20" width="56" height="4"/><rect x="2" y="46" width="56" height="4"/></g></svg>
  <h3>Heating</h3><p>Trust our professionals to listen to<br>your needs and problems</p>
</div>
<div class="abs service" style="top:935px;left:797px">
  <svg width="60" height="62" viewBox="0 0 60 62"><rect x="6" y="8" width="48" height="48" rx="4" fill="#5c2a8c"/><circle cx="30" cy="32" r="16" fill="none" stroke="#fff" stroke-width="3"/><circle cx="30" cy="32" r="4" fill="#fff"/></svg>
  <h3>Air Conditioning</h3><p>Then present you with options that fa your<br>budget and designs</p>
</div>
<div class="abs service" style="top:1150px;left:60px">
  <svg width="64" height="62" viewBox="0 0 64 62"><path d="M6 14l40 8-4 16-38-8z" fill="#5c2a8c"/><rect x="44" y="26" width="14" height="8" fill="#5c2a8c"/><rect x="22" y="34" width="4" height="18" fill="#5c2a8c"/><rect x="14" y="52" width="20" height="4" fill="#5c2a8c"/></svg>
  <h3>Security Systems</h3><p>You can view events over a monitor<br>in our home</p>
</div>
<div class="abs service" style="top:1150px;left:426px">
  <svg width="60" height="62" viewBox="0 0 60 62"><rect x="12" y="10" width="36" height="42" fill="#5c2a8c"/><rect x="20" y="18" width="20" height="26" fill="none" stroke="#fff" stroke-width="2"/><g stroke="#5c2a8c" stroke-width="3"><path d="M6 18h6M6 30h6M6 42h6M48 18h6M48 30h6M48 42h6"/></g></svg>
  <h3>Panels Changes</h3><p>Then present you with options that fa your<br>budget and designs</p>
</div>
<div class="abs service" style="top:1150px;left:797px">
  <svg width="60" height="62" viewBox="0 0 60 62"><g stroke="#5c2a8c" stroke-width="7" stroke-linecap="round"><path d="M12 50L44 18"/><path d="M14 14l32 36"/></g><circle cx="46" cy="14" r="8" fill="#5c2a8c"/></svg>
  <h3>Trouble Shooting</h3><p>Prices that meet your needs and We think before<br>we start working to budget save you money</p>
</div>

<div class="abs cta-band"></div>
<div class="abs cta-photo" role="img" aria-label="Photo of an electrician in a yellow hard hat working on a switchboard"></div>
<h3 class="abs cta-title">Do you need help with electrical maintenance?</h3>
<p class="abs cta-text">Contact us – our technicians are ready to help you solve that issue.</p>
<div class="abs cta-btn">Contact us</div>

<div class="abs sec-head" style="top:1578px"><h2>What We Do</h2><div class="sub">what we offer</div></div>
<div class="abs about-photo" role="img" aria-label="Photo of a smiling electrician in a yellow hard hat giving a thumbs up"></div>
<div class="abs about-text">
  <h3>K7 ELECTRICAL SERVICES</h3>
  <p>Lorem Ipsum is simply dummy text of the printing and typesetting industry. Lorem Ipsum has been the industry's standard dummy text ever since the 1500s, when an unknown printer took a galley of type and scrambled it to make a type specimen book. It has survived</p>
  <p>It was popularised in the 1960s with the release of transfer sheets containing Lorem Ipsum passages, and more recently with desktop publishing tools like modern layout software including versions of Lorem Ipsum.</p>
</div>
<div class="abs form">
  <h3>Contact Form</h3>
  <div class="field">*Name</div>
  <div class="field">*Email Address</div>
  <div class="field">*Phone</div>
  <div class="field msg">*Message</div>
  <span class="submit">Submit</span>
</div>

<div class="abs works"></div>
<div class="abs sec-head" style="top:2130px"><h2>Completed Works</h2><div class="sub">what we offer</div></div>
<div class="abs filters"><span class="active">All</span><span>Lighting</span><span>Ceiling Fans</span><span>Home Theaters</span></div>
<div class="abs grid">
  <div class="tile" role="img" aria-label="Photo of a portable air conditioner in a bright room" style="background:linear-gradient(160deg,#e6e1d6,#a49a86)"></div>
  <div class="tile" role="img" aria-label="Photo of ceiling spotlights on a warm wooden ceiling" style="background:linear-gradient(160deg,#7a4a2c,#c88a5a)"></div>
  <div class="tile" role="img" aria-label="Photo of a modern kitchen with under-cabinet lighting" style="background:linear-gradient(160deg,#3b2a20,#8a7868)"></div>
  <div class="tile" role="img" aria-label="Photo of a ceiling fan with lamps" style="background:linear-gradient(160deg,#d9d2c6,#9a8c7a)"></div>
  <div class="tile" role="img" aria-label="Photo of a lounge with warm wall lighting" style="background:linear-gradient(160deg,#4a3a2c,#b08d68)"></div>
  <div class="tile" role="img" aria-label="Photo of a wall-mounted air conditioning unit" style="background:linear-gradient(160deg,#e8e8e2,#9aa08a)"></div>
  <div class="tile" role="img" aria-label="Photo of a home theatre room with a large screen" style="background:linear-gradient(160deg,#cbb89a,#6d5a44)"></div>
  <div class="tile" role="img" aria-label="Photo of a metal pendant lamp with an exposed bulb" style="background:linear-gradient(160deg,#3c3a38,#8c8680)"></div>
</div>

<div class="abs sec-head" style="top:2945px"><h2>Our Testimonials</h2><div class="sub">what we offer</div></div>
<div class="abs quote-box q1">Lorem ipsum dolor sit amet, consectetur adipisicing elit, sed do eiusmod tempor incididunt ut labore et dolore magna aliqua. Ut enim ad minim veniam, quis nostrud exercitation ullamco laboris nisi ut aliquip ex ea commodo consequat. Duis aute irure dolor.</div>
<div class="abs quote-box q2">These guys solved my problem in a moment. Highly recommended!</div>
<div class="abs avatar" role="img" aria-label="Portrait photo of the reviewer" style="top:3290px;left:170px;background:linear-gradient(160deg,#c9a24a,#6b5a3a)"></div>
<div class="abs person" style="top:3304px;left:286px"><h4>Clara Whitmore</h4><p>Enginer of Media Production</p></div>
<div class="abs person" style="top:3284px;left:750px;text-align:center;width:200px"><h4>Clara Whitmore</h4><p>Enginer of Media Production</p></div>
<div class="abs avatar" role="img" aria-label="Portrait photo of the reviewer" style="top:3262px;left:962px;background:linear-gradient(160deg,#8a6a52,#3a2a22)"></div>

<div class="abs map" role="img" aria-label="Street map showing the office location with a red marker"></div>

<div class="abs footer"></div>
<div class="abs office" style="left:110px">
  <h3>Head Office</h3>
  <div class="row"><svg width="12" height="16" viewBox="0 0 12 16"><path d="M6 0a5 5 0 0 1 5 5c0 4-5 11-5 11S1 9 1 5a5 5 0 0 1 5-5z" fill="#fff"/></svg><span>2200 Linden Ave<br>Suite 310</span></div>
  <div class="row"><svg width="12" height="16" viewBox="0 0 12 16"><circle cx="6" cy="8" r="5" fill="none" stroke="#fff" stroke-width="2"/></svg><span>Westbrook, NJ 07099</span></div>
  <div class="row"><svg width="12" height="14" viewBox="0 0 12 12"><rect width="12" height="9" y="2" fill="none" stroke="#fff" stroke-width="1.5"/></svg><span>Phone: +1 (732) 555 0176</span></div>
</div>
<div class="abs divider" style="left:455px"></div>
<div class="abs office" style="left:510px">
  <h3>Head Office</h3>
  <div class="row"><svg width="12" height="16" viewBox="0 0 12 16"><path d="M6 0a5 5 0 0 1 5 5c0 4-5 11-5 11S1 9 1 5a5 5 0 0 1 5-5z" fill="#fff"/></svg><span>2200 Linden Ave<br>Suite 310</span></div>
  <div class="row"><svg width="12" height="16" viewBox="0 0 12 16"><circle cx="6" cy="8" r="5" fill="none" stroke="#fff" stroke-width="2"/></svg><span>Westbrook, NJ 07099</span></div>
  <div class="row"><svg width="12" height="14" viewBox="0 0 12 12"><rect width="12" height="9" y="2" fill="none" stroke="#fff" stroke-width="1.5"/></svg><span>Phone: +1 (732) 555 0176</span></div>
</div>
<div class="abs divider" style="left:790px"></div>
<div class="abs office" style="left:885px">
  <h3>Head Office</h3>
  <div class="row"><svg width="12" height="16" viewBox="0 0 12 16"><path d="M6 0a5 5 0 0 1 5 5c0 4-5 11-5 11S1 9 1 5a5 5 0 0 1 5-5z" fill="#fff"/></svg><span>2200 Linden Ave<br>Suite 310</span></div>
  <div class="row"><svg width="12" height="16" viewBox="0 0 12 16"><circle cx="6" cy="8" r="5" fill="none" stroke="#fff" stroke-width="2"/></svg><span>Westbrook, NJ 07099</span></div>
  <div class="row"><svg width="12" height="14" viewBox="0 0 12 12"><rect width="12" height="9" y="2" fill="none" stroke="#fff" stroke-width="1.5"/></svg><span>Phone: +1 (732) 555 0176</span></div>
</div>

<footer class="abs bottom">
  <div class="brand"><span class="mark" style="background:#bbb"></span>K7 Electrical Services Ltd</div>
  <div class="links">Home • Solutions • Services • Company • Contact</div>
  <div class="copy">Copyright © 2007 - 2018 &nbsp;K7 Electrical Services Ltd, licence number 48120736 Inc. All Rights Reserved</div>
  <div class="socials"><span></span><span></span><span></span><span></span></div>
</footer>

</body>
</html>
```